Cleaning Service Company In need of Good Web presence.

The company is a cleaning service company which provides professional staff and service for cleaning. This is a project to build a site that is both solid and a strong recognition of our organization. It is supposed to show quality, cleanliness, professionalism. The use of images and art for imagery is all good just to have a site that is consistent and solid. There might be a chance to make stationary, logo and business cars if someone feels they can build a brand that is consistent. The image we are going for is clean solid and to stand out. Finally stationary should not be expensive to print.

Current logo is attached and can be used or can be made more creative.

Target Market(s)

Corporate and Government entities, that will feel that this company has a brand that sets it apart from the rest. The company is new so the modification of the logo will not be an issue if a more solid brand come out of this project. The idea is to have a clean consistent product that stands our from others in terms of website, stationary, etc

Industry/Entity Type

Cleaning Service

Contact Information for Business Card

P.O.Box 51947
Riffa
Kingdom of Bahrain

Logo Text

Harbor Lane Services

Number of Pages Required

4 page

Font styles to use
Sans Serif

Colors
abd036
cadf82
eaf2ce
9bcb3b

Requirements
Must have
• Green Color to be used in order to stick to the name. Also the creativity and boldness in an elegant manner.
Nice to have
• Arabic name of company
• هاربر لين سرفسس ذ.م.م
• if cannot be put at least make a location should be chosen
• Also could be a bit of 3D given to the logo if it could stay elegent.
Should not have
• Should not show people cleaning.

```html
<!DOCTYPE html>
<html lang="en">
<head>
<meta charset="utf-8">
<title>Harbor Lane Services</title>
<link rel="stylesheet" href="https://fonts.googleapis.com/css2?family=Varela+Round&family=Open+Sans:wght@400;600;700&display=swap">
<style>
:root{
  --green:#abd036;
  --green-mid:#9bcb3b;
  --green-soft:#cadf82;
  --green-pale:#eaf2ce;
  --ink:#222;
  --text:#555;
  --white:#fff;
  --head:"Varela Round",sans-serif;
  --body:"Open Sans",sans-serif;
}
*{box-sizing:border-box;margin:0;padding:0}
html,body{width:1200px;height:3734px;overflow:hidden}
body{position:relative;font-family:var(--body);color:var(--text);background:var(--white)}
.abs{position:absolute}
.btn{position:absolute;background:var(--green);color:#fff;font:600 17px var(--body);border-radius:3px;text-align:center;line-height:44px;height:44px;z-index:2}
.topbar{left:0;top:0;width:1200px;height:25px;background:var(--green);color:#fff;font-size:11px;line-height:25px;padding-left:125px}
.topbar span{margin-right:18px}
.nav{left:0;top:25px;width:1200px;height:57px;background:#fff;display:flex;justify-content:center;align-items:center;gap:30px;font-size:14px;color:#444}
.nav .active{color:var(--green)}
.nav .brand{display:flex;align-items:center;gap:6px;color:var(--green);font:600 12px var(--body)}
.nav .brand i{width:22px;height:22px;border-radius:50%;background:var(--green);display:block}
.photo{position:absolute}
.hero{left:0;top:82px;width:1200px;height:441px;background:linear-gradient(120deg,#d9dcdb,#f2f3f1 45%,#c9ccca)}
.hero h1{position:absolute;top:160px;width:1200px;text-align:center;font:400 44px/1.2 var(--head);color:#555}
.dots{left:584px;top:486px;display:flex;gap:8px}
.dots i{width:8px;height:8px;border-radius:50%;background:#fff;opacity:.7;display:block}
.services-art{left:125px;top:598px;width:435px;height:323px;background:radial-gradient(circle at 50% 50%,#d8eef2,#fff 70%)}
.section-title{font:400 28px/1.1 var(--head);color:var(--ink)}
.services h2{left:627px;top:600px;width:400px}
.services p{left:627px;top:752px;width:450px;font-size:12.5px;line-height:20px}
.family{left:0;top:983px;width:1200px;height:461px;background:linear-gradient(180deg,#efeae3,#e7e1d8 60%,#b7aea1)}
.family h2{position:absolute;top:128px;width:1200px;text-align:center;font:400 40px/1.15 var(--head);color:var(--ink)}
.family p{position:absolute;top:225px;left:250px;width:700px;text-align:center;font-size:15px;line-height:20px;color:#333}
.how{left:0;top:1444px;width:1200px;height:1444px;background:var(--green-pale)}
.center{position:absolute;left:0;width:1200px;text-align:center}
.video{left:125px;top:1618px;width:448px;height:224px;background:linear-gradient(135deg,#eceeef,#fff 50%,#dfe4e1)}
.play{left:321px;top:1702px}
.accordion{left:627px;width:448px;background:#fff;border:1px solid #ddd}
.accordion h3{font:400 15px var(--head);color:var(--ink)}
.accordion p{font-size:12px;line-height:19px;margin-top:10px}
.testimonial{left:0;top:1942px;width:1200px;height:336px;background:linear-gradient(100deg,#c8b9a3,#e6ddcf 40%,#b9b3a6 70%,#d9d6cf)}
.quote-band{left:125px;top:70px;width:945px;height:187px;background:rgba(120,120,120,.45);padding:22px 26px}
.quote-band blockquote{font:400 27px/1.15 var(--head);color:#fff}
.quote-band .who{margin-top:14px;font:700 12px var(--body);color:#fff}
.quote-band .role{font-size:11px;color:#fff}
.quote-mark{left:587px;top:1998px;z-index:2}
.field{position:absolute;background:#fff;font-size:12px;color:#666;padding:12px 14px}
.blog-img{top:2958px;height:333px}
.rule{left:0;top:3366px;width:1200px;height:6px;background:var(--green-pale)}
.footer{left:0;top:3381px;width:1200px;height:316px;background:#fff}
.footer h4{font:700 15px var(--body);color:var(--green)}
.footer p,.footer li{font-size:12px;line-height:20px;color:#333}
.footer ul{list-style:none;margin-top:8px}
.footer li::before{content:"";display:inline-block;width:6px;height:6px;border-radius:50%;background:var(--green);margin-right:8px}
.bottombar{left:0;top:3697px;width:1200px;height:37px;background:var(--green);color:#fff;font-size:11px;line-height:37px;padding-left:125px}
.social{right:125px;top:3709px;display:flex;gap:16px}
.social i{width:14px;height:14px;border-radius:50%;background:#fff;display:block}
</style>
</head>
<body>
<div class="abs topbar"><span>&#9742; 0155200418</span><span>&#9993; hello@harborlane.com</span></div>
<nav class="abs nav">
  <span class="active">Home</span><span>Features</span>
  <span class="brand"><i></i>Harbor Lane Services</span>
  <span>About us</span><span>Blog</span>
</nav>

<section class="photo hero" role="img" aria-label="Bright modern white office interior with curved ceiling">
  <h1>Care your Company and Home.</h1>
</section>
<a class="btn" style="left:525px;top:316px;width:150px">Booking now !</a>
<div class="abs dots"><i></i><i></i><i></i></div>

<section class="services">
  <div class="photo services-art" role="img" aria-label="Illustration of professional cleaning equipment and supplies"></div>
  <h2 class="abs section-title">Professional Cleaning<br>Services</h2>
  <p class="abs">Regular vacuuming and stain-removal products can help, but they simply can't match the cleaning power of professional cleaning, can help remove the evidence of everyday living</p>
  <a class="btn" style="left:777px;top:843px;width:150px">Booking now!</a>
</section>

<section class="photo family" role="img" aria-label="Clean bright living room interior">
  <h2>Keep your home clean and<br>tiedy for you and your family.</h2>
  <p>You desrve a clean and tidy house it will keep you safe and protected from illness and tired safe your family.</p>
</section>
<a class="btn" style="left:527px;top:1270px;width:146px">Booking now!</a>

<section class="abs how"></section>
<h2 class="center section-title" style="top:1514px">How we do it ?</h2>
<p class="center" style="top:1555px;font-size:12px">We are doing it throw 4 steps</p>
<div class="photo video" role="img" aria-label="Close-up of a cleaning sponge on a white surface"></div>
<svg class="abs play" width="56" height="56" viewBox="0 0 56 56"><circle cx="28" cy="28" r="25" fill="none" stroke="#fff" stroke-width="3"/><path d="M22 17 L39 28 L22 39 Z" fill="#fff"/></svg>
<div class="abs accordion" style="top:1623px;height:132px;padding:16px 20px">
  <h3>What is method of cleaning ?</h3>
  <p>The method we use for cleaning is hot water extraction, commonly referred to as steam cleaning. Harborclean exclusive hot water extraction method removes the toughest, deepest dirt safely and gently.</p>
</div>
<div class="abs accordion" style="top:1775px;height:50px;padding:15px 20px;background:#f4f4f4">
  <h3>Do i need a vacume before crew arrived ?</h3>
  <svg class="abs" style="right:14px;top:18px" width="14" height="14"><circle cx="7" cy="7" r="7" fill="#bbb"/></svg>
</div>

<section class="photo testimonial" role="img" aria-label="Family relaxing together in a clean living room">
  <div class="abs quote-band">
    <blockquote>“Great Company make my own Company clean and tidy, and they call me after one week and make follow up to make everything is good”</blockquote>
    <div class="who">Sam Holloway</div>
    <div class="role">CEO, Northway Business Solutions</div>
  </div>
</section>
<svg class="abs quote-mark" width="26" height="26"><circle cx="13" cy="13" r="13" fill="#abd036"/><text x="13" y="20" text-anchor="middle" font-size="16" fill="#fff" font-family="Open Sans,sans-serif">“</text></svg>

<form>
  <div class="field" style="left:125px;top:2347px;width:460px;height:43px">Name</div>
  <div class="field" style="left:615px;top:2347px;width:460px;height:43px">Email Address</div>
  <div class="field" style="left:125px;top:2420px;width:950px;height:132px">Message</div>
  <span class="abs" style="left:872px;top:2586px;font-size:12px">13 + 7 =</span>
  <div class="field" style="left:918px;top:2574px;width:46px;height:40px"></div>
  <a class="btn" style="left:979px;top:2572px;width:96px;height:42px;line-height:42px;font-size:15px">Submit</a>
</form>

<h2 class="center" style="top:2755px;font:400 30px var(--head);color:var(--green)">Our Blog</h2>
<p class="center" style="top:2794px;font-size:12px;color:#333">Keep your self updated with our latest news.</p>
<div class="photo blog-img" style="left:67px;width:505px;background:linear-gradient(135deg,#e8eae8,#fff 55%,#e2e6e3)" role="img" aria-label="Hand holding a cleaning sponge"></div>
<div class="photo blog-img" style="left:630px;width:505px;background:linear-gradient(120deg,#cfd2d2,#f3f3f2 50%,#d6d8d7)" role="img" aria-label="Cleaned modern office corridor"></div>

<div class="abs rule"></div>
<footer class="abs footer">
  <div class="abs" style="left:125px;top:70px;width:220px;display:flex;align-items:center;gap:8px">
    <svg width="24" height="24"><circle cx="12" cy="12" r="12" fill="#abd036"/></svg>
    <span style="font:700 14px var(--body);color:var(--green)">Harbor Lane Services</span>
  </div>
  <div class="abs" style="left:373px;top:72px;width:210px">
    <h4>About Us</h4>
    <p style="margin-top:8px">With over 10 years of experience in the cleaning industry our reputation has grown and grown. And we owe it all to you, our clients.</p>
  </div>
  <div class="abs" style="left:627px;top:72px">
    <h4>Important links</h4>
    <ul><li>Home</li><li>Features</li><li>About us</li><li>Blog</li></ul>
  </div>
  <div class="abs" style="left:876px;top:72px;width:200px">
    <h4 style="color:var(--ink);font:400 18px/1.1 var(--head)">Contact<br>information</h4>
    <p style="margin-top:8px">Address: 14 Palm Road, Riffa, Bahrain<br>P.O.Box 51947<br>Phone: 1 800 555 0142</p>
  </div>
</footer>
<div class="abs bottombar">Powered by Brightline Studio</div>
<div class="abs social"><i></i><i></i><i></i></div>
</body>
</html>
```